Business Cards for IT Consulting Company (Managed Service Provider)

I am looking to have some business cards printed and would like some designs. We are an IT Consulting company based in Vancouver BC. I would like a nice clean and modern look to the cards. I have uploaded all the versions of my logo so parts can be used as needed. Here is a snippit from our website homepage:

Quillbrook Networks Ltd. is an IT Solutions Partner located in Vancouver BC, Canada. We offer IT solutions and support to customers in the greater Vancouver Area. With expertise in Microsoft platforms, as well as Linux and Mac OSX and over 12 years experience in the IT industry, Quillbrook Networks is dedicated to offering our clients top quality service and products. We take pride in the solutions we offer our customers. The greatest compliment a client can give us is to recommend our services.

Quillbrook Networks Ltd. offers a wide range of IT services from onsite service to remote support and managed service solutions. This allows clients to choose the support path that best suits their company’s needs. Supporting many different sized companies from small to enterprise level over the past 12 years Quillbrook Networks has the experience and expertise needed to ensure things run smoothly. Allowing our clients to focus on doing business.

Revolutionizing the way IT services are delivered.

Quillbrook Networks is dedicated to providing our clients with IT solutions that work and grow with them for years to come. This philosophy helps save money in the long run instead of replacing equipment constantly. Far too often IT solutions are not well thought out and while possibly solving the problem at hand, require replacement due to growth or quality within a very short time frame. Quillbrook Networks takes pride in providing solutions that will last and be able to accommodate growth without the need for replacement.

Industry/Entity Type

Information Technology

Contact Information for Business Card

Quillbrook Networks Ltd.
(Employee Name)
Eml: (Employees Email Address)
Web: quillbrook.me
Ph: 604-555-0148

Font styles to use
Serif
Sans Serif

Requirements
Must have
• The Company logo and company colors.
Nice to have
• - Our tag line: "Revolutionizing IT Services" or "Revolutionizing the way IT services are delivered."
• - Also I really like the idea of nature and technology together blending which is sort of where my logo came from so integrating that somehow onto the business cards would be great.

```html
<!DOCTYPE html>
<html lang="en">
<head>
<meta charset="utf-8">
<title>Quillbrook Networks Ltd. – Business Card</title>
<link rel="stylesheet" href="https://fonts.googleapis.com/css2?family=Montserrat:wght@500;600&family=Open+Sans:wght@400&display=swap">
<style>
  :root {
    --page-bg: #e9ecef;
    --card-black: #0b0c0e;
    --card-edge: #202226;
    --brand-blue: #2a9be6;
    --name-grey: #6b6e73;
    --contact-text: #c9d6e2;
    --address-blue: #2f6f9e;
    --band-top: #1f7fc4;
    --band-bottom: #0f4f86;
    --rule: #3a3d42;
  }
  * { margin: 0; padding: 0; box-sizing: border-box; }
  html, body {
    width: 1200px; height: 900px; overflow: hidden;
    background: var(--page-bg);
  }
  .business-card {
    position: absolute;
    left: 120px; top: 177px;
    width: 960px; height: 546px;
    background:
      radial-gradient(ellipse at 62% 40%, rgba(70,74,80,0.35), transparent 60%),
      linear-gradient(180deg, var(--card-edge) 0%, var(--card-black) 45%, var(--card-black) 100%);
    box-shadow: 0 18px 40px rgba(0,0,0,0.28);
    overflow: hidden;
    font-family: "Open Sans", Arial, sans-serif;
  }
  .brand {
    position: absolute; left: 42px; top: 46px;
    display: flex; align-items: center; gap: 26px;
    color: var(--brand-blue);
    font-family: "Montserrat", Arial, sans-serif;
    font-weight: 500;
  }
  .brand-square {
    width: 64px; height: 64px;
    border: 4px solid var(--brand-blue);
  }
  .brand-name { font-size: 72px; line-height: 0.95; letter-spacing: -1px; }
  .brand-suffix { font-size: 27px; line-height: 1.1; letter-spacing: 0.5px; }
  .person {
    position: absolute; left: 42px; top: 228px;
    font-family: "Montserrat", Arial, sans-serif;
    font-weight: 600; font-size: 36px;
    display: flex; align-items: baseline; gap: 14px;
  }
  .person-first { color: var(--brand-blue); }
  .person-last { color: var(--name-grey); margin-left: -4px; }
  .person-sep { color: var(--name-grey); font-weight: 500; }
  .person-role {
    color: var(--brand-blue);
    font-family: "Open Sans", Arial, sans-serif;
    font-weight: 400; font-size: 21px;
  }
  .contact-band { position: absolute; left: 0; top: 282px; }
  .contact-list {
    position: absolute; left: 40px; top: 318px;
    list-style: none;
    color: var(--contact-text);
    font-size: 22px; letter-spacing: 0.5px;
  }
  .contact-list li {
    display: flex; align-items: center; gap: 12px;
    height: 39px;
  }
  .contact-icon { width: 22px; height: 22px; flex: none; }
  .address {
    position: absolute; left: 77px; top: 488px;
    color: var(--address-blue);
    font-size: 22px; letter-spacing: 0.8px;
  }
</style>
</head>
<body>
  <div class="business-card">
    <div class="brand">
      <div class="brand-square"></div>
      <div class="brand-text">
        <div class="brand-name">quillbrook</div>
        <div class="brand-suffix">NETWORKS LTD.</div>
      </div>
    </div>

    <div class="person">
      <span class="person-first">Dana</span>
      <span class="person-last">Whitlock</span>
      <span class="person-sep">|</span>
      <span class="person-role">Director</span>
    </div>

    <svg class="contact-band" width="960" height="190" viewBox="0 0 960 190" aria-hidden="true">
      <defs>
        <linearGradient id="bandFill" x1="0" y1="0" x2="0" y2="1">
          <stop offset="0" stop-color="var(--band-top)"/>
          <stop offset="1" stop-color="var(--band-bottom)"/>
        </linearGradient>
      </defs>
      <line x1="0" y1="1" x2="610" y2="1" stroke="var(--rule)" stroke-width="2"/>
      <polygon points="0,6 610,6 565,96 610,186 0,186" fill="url(#bandFill)" opacity="0.9"/>
      <line x1="0" y1="189" x2="610" y2="189" stroke="var(--rule)" stroke-width="2"/>
    </svg>

    <ul class="contact-list">
      <li>
        <svg class="contact-icon" viewBox="0 0 24 24" aria-hidden="true"><path fill="#0b0c0e" d="M3 9c0-3 4-5 9-5s9 2 9 5l-4 1-1-3H8L7 10 3 9zm4 2h10l2 9H5l2-9zm5 2a3 3 0 1 0 0 6 3 3 0 0 0 0-6z"/></svg>
        <span>604-555-0148</span>
      </li>
      <li>
        <svg class="contact-icon" viewBox="0 0 24 24" aria-hidden="true"><rect x="2" y="5" width="20" height="14" fill="#0b0c0e"/><path d="M2 5l10 8 10-8" fill="none" stroke="#4d8fc2" stroke-width="1.5"/></svg>
        <span>dana@quillbrooknetworks.com</span>
      </li>
      <li>
        <svg class="contact-icon" viewBox="0 0 24 24" aria-hidden="true"><circle cx="12" cy="12" r="10" fill="#0b0c0e"/><path d="M2 12h20M12 2c-4 5-4 15 0 20M12 2c4 5 4 15 0 20" fill="none" stroke="#4d8fc2" stroke-width="1.2"/></svg>
        <span>www.quillbrooknetworks.com</span>
      </li>
    </ul>

    <div class="address">18 Ashgrove Road, Kelso VIC 3188</div>
  </div>
</body>
</html>
```